Business card

We need a business card design for our company based in Auckland , New Zealand called 'Ridge + Studio Ltd'. We provide architectural services. We would like to see designs that use the max. three colours (such as white, black, grey) The final design should communicate financial safety and growth."
Also I will provide our company logo. I would like to the logo to be embeded onto our business card.

Target Market(s)

new residential house, alteration & addition & light commericila design & drafting service

Industry/Entity Type

Architecture

Contact Information for Business Card

Company name: ridge + studio Ltd.
Name: Mark Delford
Job title: architectural designer & Design LBP
email address: mark@rplusd.co.nz
mobile number: 02 5163 2290
web site: www.rplusd.co.nz

Requirements
Must have
• My project must have..
• - embeded logo (attached company logo)
• I don't have a bigger version for our company logo, but I have one old one, so you can remove the word from it)
• - insert the attached small BKTW logo & LBP logo
• - creative, simple and clear business card.
• - Max. three colours
Nice to have
• - Here are the samples I would like to share with you: http://www.plimvora.com/blog/minimalistic-business-card-designs/
• I would like to have my business card like one of the creation.
Should not have
• TBA

```html
<!DOCTYPE html>
<html lang="en">
<head>
<meta charset="utf-8">
<title>Ridge + Studio Ltd — Business Card</title>
<link rel="stylesheet" href="https://fonts.googleapis.com/css2?family=Open+Sans:wght@400;600;700&display=swap">
<style>
  :root {
    --backdrop: #3b3c3e;
    --card: #f1f1f0;
    --ink: #1c1c1c;
    --ink-soft: #2e2e2e;
    --rule: #8a8a8a;
  }
  * { box-sizing: border-box; margin: 0; padding: 0; }
  html, body {
    width: 1200px;
    height: 950px;
    overflow: hidden;
    background: var(--backdrop);
    font-family: "Open Sans", Arial, sans-serif;
  }
  .canvas {
    width: 1200px;
    height: 950px;
    display: flex;
    flex-direction: column;
    align-items: center;
    justify-content: center;
    gap: 44px;
  }
  .card {
    position: relative;
    width: 700px;
    height: 420px;
    background: var(--card);
    color: var(--ink);
    box-shadow: 0 6px 18px rgba(0,0,0,0.35);
  }

  /* Front */
  .card-front .contact {
    position: absolute;
    left: 58px;
    top: 62px;
  }
  .contact .name {
    font-size: 30px;
    font-weight: 700;
    letter-spacing: 0.5px;
    text-transform: uppercase;
    line-height: 1.1;
  }
  .contact .role {
    font-size: 22px;
    font-weight: 400;
    line-height: 1.22;
    margin-top: 6px;
    color: var(--ink-soft);
  }
  .contact .divider {
    width: 30px;
    height: 2px;
    background: var(--ink);
    margin: 10px 0 12px;
  }
  .contact .company {
    font-size: 17px;
    font-weight: 700;
    margin-bottom: 6px;
  }
  .contact .detail {
    font-size: 17px;
    font-weight: 400;
    line-height: 1.32;
    color: var(--ink-soft);
  }
  .card-front .brand {
    position: absolute;
    right: 58px;
    top: 118px;
    display: flex;
    flex-direction: column;
    align-items: center;
    gap: 12px;
  }
  .brand .brand-dot {
    width: 74px;
    height: 74px;
    border: 3px solid var(--ink);
    border-radius: 50%;
  }
  .brand .brand-name {
    font-size: 16px;
    font-weight: 600;
    color: var(--ink);
  }

  /* Back */
  .card-back {
    display: flex;
    align-items: center;
    justify-content: center;
    gap: 34px;
  }
  .card-back .partner-name {
    font-size: 58px;
    font-weight: 700;
    color: var(--ink-soft);
    letter-spacing: -1px;
  }
  .card-back .separator {
    width: 1px;
    height: 110px;
    background: var(--rule);
  }
  .card-back .badge { display: block; }
</style>
</head>
<body>
<main class="canvas">
  <section class="card card-front" aria-label="Business card front">
    <div class="contact">
      <p class="name">Mark Delford</p>
      <p class="role">architectural designer &amp;<br>Design LBP</p>
      <div class="divider"></div>
      <p class="company">ridge + studio Ltd.</p>
      <p class="detail">02 5163 2290</p>
      <p class="detail">mark@rplusd.co.nz</p>
      <p class="detail">www.rplusd.co.nz</p>
    </div>
    <div class="brand">
      <span class="brand-dot"></span>
      <span class="brand-name">ridge + studio</span>
    </div>
  </section>

  <section class="card card-back" aria-label="Business card back">
    <span class="partner-name">BKTW</span>
    <span class="separator"></span>
    <svg class="badge" width="110" height="110" viewBox="0 0 110 110" role="img" aria-label="Licensed practitioner certification badge">
      <circle cx="55" cy="55" r="52" fill="var(--ink)"/>
    </svg>
  </section>
</main>
</body>
</html>
```